Automotive eCommerce Business looking for a business card design

Looking for a clean and simple business card design. Our company name is "Brindle Auto" and we are a company specializing in the ecommerce sales of automotive parts, specifically for pick up trucks and large SUVs. Our company colours are red, black, and white.

Feel free to use the logo provided or create a new logo that you seem fit. Looking forward to your creative ideas!

Industry/Entity Type

Automotive

Contact Information for Business Card

We were thinking of a possibly two-sided design featuring just the logo and company name on one side, and personal information on the other side. Single sided designs will be considered as well.

Font styles to use
Serif
Sans Serif
Decorative

Colors
ec1f27
ffffff
000000

Requirements
Must have
• Space for employee's name, title, phone number and email address, along with the company address and website somewhere.

```html
<!DOCTYPE html>
<html lang="en">
<head>
<meta charset="utf-8">
<title>Brindle Auto Ltd – Business Card</title>
<link href="https://fonts.googleapis.com/css2?family=Cinzel:wght@400&family=PT+Sans:wght@400;700&display=swap" rel="stylesheet">
<style>
  :root {
    --stage: #000000;
    --card-red: #a31e23;
    --ink-white: #ffffff;
    --serif: "Cinzel", serif;
    --sans: "PT Sans", sans-serif;
  }
  * { margin: 0; padding: 0; box-sizing: border-box; }
  html, body { width: 1200px; height: 900px; overflow: hidden; background: var(--stage); }
  .stage { position: relative; width: 1200px; height: 900px; }

  .card {
    position: absolute;
    background: var(--card-red);
    color: var(--ink-white);
  }
  .card--front {
    left: 116px; top: 275px; width: 477px; height: 293px;
    border-radius: 0 52px 0 52px;
  }
  .card--back {
    left: 622px; top: 276px; width: 477px; height: 292px;
    border-radius: 60px 0 60px 0;
  }

  .brand { position: absolute; text-align: center; font-family: var(--serif); font-weight: 400; color: var(--ink-white); white-space: nowrap; }
  .brand__dot { display: block; margin: 0 auto; background: var(--ink-white); border-radius: 50%; }
  .brand__name { display: block; letter-spacing: 0.02em; }

  .card--front .brand { left: 22px; top: 36px; width: 220px; }
  .card--front .brand__dot { width: 70px; height: 70px; }
  .card--front .brand__name { font-size: 20px; margin-top: 22px; }

  .card--back .brand { left: 68px; top: 62px; width: 340px; }
  .card--back .brand__dot { width: 114px; height: 114px; }
  .card--back .brand__name { font-size: 29px; margin-top: 30px; }

  .person { position: absolute; right: 19px; top: 34px; text-align: right; font-family: var(--sans); }
  .person__name { font-size: 19px; font-weight: 700; line-height: 22px; }
  .person__title { font-size: 13px; line-height: 17px; }

  .address { position: absolute; right: 21px; top: 157px; text-align: right; font-family: var(--sans); font-size: 13px; line-height: 17px; }

  .contacts { position: absolute; right: 19px; top: 216px; list-style: none; font-family: var(--sans); font-size: 13px; line-height: 17.5px; }
  .contacts li { display: flex; justify-content: flex-end; align-items: center; gap: 7px; }
  .contacts svg { width: 11px; height: 11px; fill: var(--ink-white); flex: none; }
</style>
</head>
<body>
<main class="stage">
  <section class="card card--front">
    <div class="brand">
      <span class="brand__dot"></span>
      <span class="brand__name">Brindle Auto Ltd</span>
    </div>
    <div class="person">
      <p class="person__name">Marcus Hale</p>
      <p class="person__title">Managing Director</p>
    </div>
    <address class="address" style="font-style:normal">
      12345, Address Goes Here<br>Country Name, 123456
    </address>
    <ul class="contacts">
      <li>044-123 456 789
        <svg viewBox="0 0 24 24" aria-hidden="true"><path d="M6.6 10.8a15.1 15.1 0 0 0 6.6 6.6l2.2-2.2a1 1 0 0 1 1-.25 11.4 11.4 0 0 0 3.6.57 1 1 0 0 1 1 1V20a1 1 0 0 1-1 1A17 17 0 0 1 3 4a1 1 0 0 1 1-1h3.5a1 1 0 0 1 1 1c0 1.25.2 2.45.57 3.57a1 1 0 0 1-.25 1z"/></svg>
      </li>
      <li>info@brindlemail.com
        <svg viewBox="0 0 24 24" aria-hidden="true"><path d="M2 5h20v14H2z M2 5l10 8 10-8" fill="#fff"/><path d="M3 6l9 7 9-7" fill="none" stroke="#a31e23" stroke-width="2"/></svg>
      </li>
      <li>www.brindleparts.com
        <svg viewBox="0 0 24 24" aria-hidden="true"><path d="M10 14a4 4 0 0 1 0-5.6l3-3a4 4 0 0 1 5.6 5.6l-1.5 1.5M14 10a4 4 0 0 1 0 5.6l-3 3a4 4 0 0 1-5.6-5.6l1.5-1.5" fill="none" stroke="#fff" stroke-width="2.4" stroke-linecap="round"/></svg>
      </li>
    </ul>
  </section>

  <section class="card card--back">
    <div class="brand">
      <span class="brand__dot"></span>
      <span class="brand__name">Brindle Auto Ltd</span>
    </div>
  </section>
</main>
</body>
</html>
```